Ductless Mini Split Business Website

Copper Fern Services is looking to design an eye catching educational website about installing Ductless mini splits.

Similar to this company.
https://www.halvikstream.com/

Coding

Coded - Design and coding required

```html
<!DOCTYPE html>
<html lang="en">
<head>
<meta charset="utf-8">
<title>Copper Fern Services – Ductless Experts</title>
<link href="https://fonts.googleapis.com/css2?family=Roboto:wght@400;500;700&family=Roboto+Slab:wght@400;500&family=Bungee+Outline&display=swap" rel="stylesheet">
<style>
:root{
  --yellow:#f5c518;
  --yellow-deep:#e9b308;
  --ink:#1b1b1b;
  --dark:#2a2a2a;
  --grey:#e9e9e9;
  --muted:#777;
  --white:#fff;
}
*{box-sizing:border-box;margin:0;padding:0}
html,body{width:1200px;height:4458px;overflow:hidden;background:var(--white)}
body{position:relative;font-family:"Roboto",sans-serif;color:var(--ink)}
.abs{position:absolute}
.fill{position:absolute}

/* header */
.logo{left:78px;top:30px;display:flex;align-items:center;gap:10px}
.logo-dot{width:34px;height:34px;border-radius:50%;background:var(--yellow)}
.logo-name{font-family:"Roboto",sans-serif;font-weight:700;font-size:16px;line-height:1.15;color:var(--ink);text-transform:uppercase;width:150px}
.socials{left:744px;top:38px;display:flex;gap:14px}
.socials span{width:36px;height:36px;border-radius:50%;background:#3d8fd8;border:3px solid #d9d9d9}
.callbox{left:908px;top:30px;width:215px;height:52px;background:var(--yellow);clip-path:polygon(0 0,94% 0,100% 50%,94% 100%,0 100%)}
.callbox .ic{position:absolute;left:10px;top:10px;width:32px;height:32px;border-radius:50%;background:var(--ink)}
.callbox small{position:absolute;left:70px;top:9px;font:400 11px "Roboto Slab",serif;color:#4a3a00}
.callbox b{position:absolute;left:70px;top:24px;font:500 16px "Roboto Slab",serif}
.nav{left:78px;top:114px;width:1044px;height:54px;background:var(--dark);display:flex;align-items:center;clip-path:polygon(0 0,100% 0,98.5% 50%,100% 100%,0 100%,1.5% 50%)}
.nav a{color:#ddd;font:400 14px "Roboto",sans-serif;letter-spacing:.5px;text-decoration:none;margin-right:43px}
.nav .home{background:var(--yellow);color:var(--ink);height:54px;width:122px;display:flex;align-items:center;justify-content:center;margin-right:40px;clip-path:polygon(0 0,88% 0,100% 100%,0 100%)}
.nav .contact{margin-left:auto;background:#111;color:#fff;height:54px;width:170px;display:flex;align-items:center;justify-content:center;margin-right:0}

/* buttons */
.btn{position:absolute;height:52px;display:flex;align-items:center;background:var(--ink);color:#fff;font:400 15px "Roboto Slab",serif;text-transform:uppercase;clip-path:polygon(0 0,94% 0,100% 50%,94% 100%,0 100%)}
.btn::before{content:"";width:52px;height:52px;background:var(--yellow);clip-path:polygon(50% 0,100% 50%,50% 100%,0 50%);margin-right:18px}
.btn.light{background:var(--white);color:var(--ink)}

/* hero */
.hero{left:0;top:140px;width:1200px;height:752px;background:linear-gradient(180deg,#d9d4cc 0%,#c5beb2 55%,#8d7f70 100%)}
.hero-box{left:210px;top:312px;width:780px;height:280px;background:rgba(255,255,255,.72);text-align:center}
.hero-box h1{font:400 44px "Bungee Outline",sans-serif;color:var(--ink);margin-top:40px}
.hero-box p{font:400 18px/1.6 "Roboto",sans-serif;width:720px;margin:14px auto 0}

.sec-title{position:absolute;width:1200px;text-align:center;font:500 34px "Roboto",sans-serif;text-transform:uppercase}

/* service cards */
.card{position:absolute;top:1088px;width:240px;height:367px;background:linear-gradient(180deg,#444 45%,#050505 100%);color:#fff;text-align:center}
.card.active{background:linear-gradient(180deg,var(--yellow) 45%,var(--yellow-deep) 100%);color:var(--ink)}
.card .ph{height:168px;background:linear-gradient(135deg,#dfe3e6,#9aa4ab)}
.card h3{font:400 19px/1.4 "Roboto Slab",serif;margin-top:26px}
.card p{font:400 14px/1.85 "Roboto",sans-serif;margin:12px 14px 0}
.card .badge{position:absolute;left:84px;top:-50px;width:72px;height:72px;border-radius:50%;background:#333;border:5px solid #fff;box-shadow:0 2px 6px rgba(0,0,0,.3)}
.card .badge svg{width:40px;height:40px;margin:11px}
.card.active .badge{background:var(--yellow)}

/* about */
.about-dark{left:0;top:1602px;width:1200px;height:286px;background:#2b2b2b;clip-path:polygon(0 0,30% 20%,100% 25%,100% 100%,0 100%)}
.about-yellow{left:0;top:1602px;width:1200px;height:130px;background:var(--yellow);clip-path:polygon(0 0,45% 65%,0 56%)}
.about-title{top:1745px;color:#fff}
.mascot{left:945px;top:1780px;width:170px;height:140px;background:radial-gradient(ellipse at 50% 50%,#f5c518 0%,#e9b308 45%,rgba(43,43,43,0) 70%)}
.about-img{left:78px;top:1836px;width:562px;height:363px;background:linear-gradient(135deg,#a9684a,#c8c2b4 60%,#49597d)}
.about-box{left:560px;top:1971px;width:562px;height:363px;background:linear-gradient(180deg,var(--yellow),var(--yellow-deep))}
.about-box h2{position:absolute;left:54px;top:55px;font:italic 400 27px/1.4 "Roboto Slab",serif}
.about-box p{position:absolute;left:54px;top:155px;width:470px;font:400 14px/1.85 "Roboto",sans-serif;color:#3a2e00}
.see-why{left:78px;top:2240px;font:500 19px/1.6 "Roboto Slab",serif;text-transform:uppercase}
.see-why span{color:var(--yellow-deep)}

/* stand behind */
.stand-bg{left:0;top:2397px;width:1200px;height:428px;background:linear-gradient(90deg,#efefef,#e3e3e3)}
.stand-title{position:absolute;left:78px;top:2455px;font:500 35px/1.3 "Roboto",sans-serif;text-transform:uppercase;color:var(--ink)}
.stand-p{left:78px;top:2570px;width:490px;font:400 15px/1.75 "Roboto",sans-serif;color:#666}
.stand-img{left:684px;top:2470px;width:380px;height:355px;background:linear-gradient(180deg,#f0f0f0 0%,#d6d9dc 35%,#2f5aa8 60%,#244a90 100%)}

.call{left:0;top:2870px;width:1200px;display:flex;justify-content:center;align-items:center;gap:20px}
.call b{font:500 21px "Roboto Slab",serif}
.call .num{font:400 35px "Roboto Slab",serif;color:var(--yellow-deep)}

.h-left{left:78px;top:2968px;font:500 35px "Roboto",sans-serif;text-transform:uppercase}
.h-right{left:624px;top:2968px;font:500 35px "Roboto",sans-serif;text-transform:uppercase}
.client-ph{left:78px;top:3053px;width:268px;height:272px;background:linear-gradient(135deg,#8a7a6c,#dfe6ec 60%,#3c6fb0)}
.fb-card{left:211px;top:3221px;width:334px;height:291px;background:#fff;border-left:4px solid var(--yellow);box-shadow:0 0 12px rgba(0,0,0,.12);text-align:center}
.fb-card h4{font:400 16px "Roboto Slab",serif;margin-top:52px}
.fb-card small{display:block;font:400 12px "Roboto",sans-serif;color:#555;margin-top:6px}
.fb-card p{font:400 15px/1.75 "Roboto",sans-serif;color:#888;margin:38px 20px 0}
.arrows{left:481px;top:3221px;display:flex}
.arrows span{width:32px;height:32px;background:var(--yellow);display:flex;align-items:center;justify-content:center;border-right:1px solid #c99c00}

.why{position:absolute;left:623px;width:499px;height:125px;background:#0d0d0d;color:#fff}
.why .c{position:absolute;left:20px;top:12px;width:100px;height:100px;border-radius:50%;background:#fff;display:flex;align-items:center;justify-content:center}
.why .c span{width:80px;height:80px;border-radius:50%;background:var(--yellow);display:flex;align-items:center;justify-content:center}
.why h4{position:absolute;left:185px;top:22px;font:400 19px "Roboto Slab",serif}
.why p{position:absolute;left:185px;top:58px;width:290px;font:400 14px/1.6 "Roboto",sans-serif;color:#aaa}

/* newsletter */
.news{left:0;top:3585px;width:1200px;height:367px;background:#3a3632}
.news-y1{left:0;top:3585px;width:1200px;height:367px;background:var(--yellow);clip-path:polygon(48% 100%,100% 100%,100% 52%)}
.news-y2{left:0;top:3585px;width:1200px;height:367px;background:var(--yellow);clip-path:polygon(0 0,100% 0,100% 8%,55% 28%,0 18%)}
.news-y3{left:0;top:3585px;width:1200px;height:367px;background:var(--yellow);clip-path:polygon(0 72%,45% 88%,0 100%)}
.news-title{top:3683px;color:#fff}
.inp{position:absolute;top:3754px;height:50px;border:1px solid #aaa;background:rgba(255,255,255,.15);color:#eee;font:400 15px "Roboto",sans-serif;padding:15px 18px}

/* footer */
.f-logo{left:78px;top:4000px}
.f-contact{left:78px;top:4102px;font:400 14px/1.6 "Roboto",sans-serif;color:#777}
.f-contact div{display:flex;gap:20px;margin-bottom:18px}
.f-contact svg{flex:none}
.f-col{position:absolute;top:3988px}
.f-col h5{font:500 17px "Roboto",sans-serif;margin-bottom:22px}
.f-col li{list-style:none;font:400 14px "Roboto",sans-serif;color:#888;margin-bottom:21px}
.f-inp{position:absolute;left:883px;width:239px;height:40px;border:1px solid #ccc;border-radius:20px;font:400 13px "Roboto",sans-serif;color:#666;padding:11px 16px}
.copy{left:0;top:4366px;width:1200px;border-top:1px solid #e5e5e5;padding-top:42px;text-align:center;font:400 11px "Roboto",sans-serif;color:#aaa}
</style>
</head>
<body>

<!-- header -->
<div class="abs logo"><span class="logo-dot"></span><span class="logo-name">Copper Fern Services</span></div>
<div class="fill" role="img" aria-label="Flying bee mascot with dotted trail" style="left:530px;top:25px;width:120px;height:60px;background:radial-gradient(ellipse at 20% 50%,#f5c518 18%,transparent 20%)"></div>
<div class="abs socials"><span></span><span></span><span></span></div>
<div class="abs callbox"><span class="ic"></span><small>Call Us Now</small><b>123.456.7890</b></div>
<nav class="abs nav">
  <a class="home">HOME</a><a>ABOUT US</a><a>SERVICES</a><a>WHY CHOOSE US</a><a>TESTIMONIALS</a><a>BLOG</a>
  <svg width="18" height="18" viewBox="0 0 18 18" style="margin-right:30px"><circle cx="7" cy="7" r="5.5" fill="none" stroke="#ddd" stroke-width="2"/><path d="M11 11l5 5" stroke="#ddd" stroke-width="2"/></svg>
  <a class="contact">CONTACT US</a>
</nav>

<!-- hero -->
<div class="fill hero" role="img" aria-label="Woman relaxing on a sofa with a laptop under a wall-mounted ductless unit"></div>
<div class="abs hero-box">
  <h1>DUCTLESS DOES IT BETTER</h1>
  <p>Lorem ipsum dolor sit amet, consectetur adipiscing elit, sed do eiusmod tempor incididunt ut labore et dolore magna aliqua.</p>
</div>
<div class="btn" style="left:488px;top:500px;width:222px">Learn More</div>

<!-- services -->
<h2 class="sec-title" style="top:943px">How Can We Help You?</h2>
<div class="card" style="left:78px"><div class="badge"><svg viewBox="0 0 40 40"><circle cx="20" cy="20" r="10" fill="none" stroke="#fff" stroke-width="3"/></svg></div><div class="ph" role="img" aria-label="Technician installing an indoor unit"></div><h3>Ductless<br>Installation</h3><p>Lorem ipsum dolor amet, consectetur adipiscing elit magna aliqua.</p></div>
<div class="card active" style="left:345px"><div class="badge"><svg viewBox="0 0 40 40"><rect x="9" y="10" width="22" height="20" fill="none" stroke="#1b1b1b" stroke-width="3"/></svg></div><div class="ph" role="img" aria-label="Technician checking a unit with a clipboard"></div><h3>Ductless<br>Maintenance</h3><p>Lorem ipsum dolor amet, consectetur adipiscing elit magna aliqua.</p></div>
<div class="card" style="left:614px"><div class="badge"><svg viewBox="0 0 40 40"><path d="M12 8v24M20 8v24M28 8v24" stroke="#fff" stroke-width="3"/></svg></div><div class="ph" role="img" aria-label="Workers repairing outdoor units"></div><h3>Ductless<br>Repair</h3><p>Lorem ipsum dolor amet, consectetur adipiscing elit magna aliqua.</p></div>
<div class="card" style="left:883px"><div class="badge"><svg viewBox="0 0 40 40"><rect x="8" y="10" width="24" height="20" rx="3" fill="none" stroke="#fff" stroke-width="3"/></svg></div><div class="ph" role="img" aria-label="Technician replacing a heat unit outdoors"></div><h3>Baseboard Heat<br>Replacement</h3><p>Lorem ipsum dolor amet, consectetur adipiscing elit magna aliqua.</p></div>
<div class="btn" style="left:470px;top:1506px;width:260px">View All Services</div>

<!-- about -->
<div class="fill about-dark"></div>
<div class="fill about-yellow"></div>
<h2 class="sec-title about-title">About Company</h2>
<div class="fill mascot" role="img" aria-label="Bee mascot holding tools"></div>
<div class="fill about-img" role="img" aria-label="Two technicians servicing an outdoor condenser by a brick wall"></div>
<div class="abs about-box">
  <h2>Helping Portland &amp; Surrounding<br>Areas Go Ductless</h2>
  <p>Lorem ipsum dolor sit amet, consectetur adipiscing elit, sed do eiusmod tempor incididunt ut labore et dolore magna of aliqua. Ut enim ad minim veniam, quis nostrud.</p>
</div>
<div class="btn light" style="left:612px;top:2230px;width:198px">Learn More</div>
<div class="abs see-why">See Why Copper Fern Ductless Experts<br><span>Could Be Right For You</span></div>

<!-- stand behind -->
<div class="fill stand-bg"></div>
<h2 class="stand-title">We Stand Behind Our<br>Ductless Services</h2>
<p class="abs stand-p">Lorem ipsum dolor sit amet, consectetur adipiscing elit, sed does eiusmod tempor incididunt ut labore et dolore magna aliqua. Utt enim ad minim veniam, quis nostrud exercitation ullamco laboris nisi ut aliquip ex ea commodo consequat.</p>
<div class="btn" style="left:78px;top:2710px;width:260px">Get A Free Quote</div>
<div class="fill stand-img" role="img" aria-label="Technician in blue overalls opening an indoor unit"></div>

<div class="abs call"><b>Call Us Today To Get a Free Estimation</b>
<svg width="34" height="34" viewBox="0 0 24 24"><path d="M6.6 10.8a15 15 0 006.6 6.6l2.2-2.2c.3-.3.7-.4 1-.2 1.1.4 2.3.6 3.6.6.6 0 1 .4 1 1V20c0 .6-.4 1-1 1A17 17 0 013 4c0-.6.4-1 1-1h3.5c.6 0 1 .4 1 1 0 1.3.2 2.5.6 3.6.1.3 0 .7-.2 1z" fill="#e9b308"/></svg>
<span class="num">123.456.7890</span></div>

<!-- feedback / why -->
<h2 class="abs h-left">Client Feedback</h2>
<h2 class="abs h-right">Why Choose Us?</h2>
<div class="fill client-ph" role="img" aria-label="Client portrait"></div>
<div class="abs fb-card">
  <h4>- Client Name</h4><small>Lorem Ipsum</small>
  <p>Lorem ipsum dolor sit consectetur adipiscing elit, sed do eiusmod tempor enim ad minim veniam, quis nostrud commodo consequat.</p>
</div>
<div class="abs arrows">
  <span><svg width="10" height="14"><path d="M8 1L2 7l6 6" stroke="#1b1b1b" stroke-width="2" fill="none"/></svg></span>
  <span><svg width="10" height="14"><path d="M2 1l6 6-6 6" stroke="#1b1b1b" stroke-width="2" fill="none"/></svg></span>
</div>

<div class="why" style="top:3053px"><div class="c"><span><svg width="40" height="40" viewBox="0 0 40 40"><path d="M6 18L20 6l14 12v16H6z" fill="none" stroke="#1b1b1b" stroke-width="3"/></svg></span></div><h4>0% Financing for 60 months</h4><p>Lorem ipsum dolor sit consectetur incididunt dolore magna aliqua.</p></div>
<div class="why" style="top:3221px"><div class="c"><span><svg width="40" height="40" viewBox="0 0 40 40"><rect x="5" y="10" width="30" height="20" fill="none" stroke="#1b1b1b" stroke-width="3"/></svg></span></div><h4>365 Day, Money Back Guarantee</h4><p>Lorem ipsum dolor sit consectetur incididunt dolore magna aliqua.</p></div>
<div class="why" style="top:3387px"><div class="c"><span><svg width="40" height="40" viewBox="0 0 40 40"><rect x="4" y="12" width="22" height="16" fill="none" stroke="#1b1b1b" stroke-width="3"/><path d="M26 17h6l4 5v6H26" fill="none" stroke="#1b1b1b" stroke-width="3"/></svg></span></div><h4>Experts in Ductless Services</h4><p>Lorem ipsum dolor sit consectetur incididunt dolore magna aliqua.</p></div>

<!-- newsletter -->
<div class="fill news" role="img" aria-label="Family relaxing in a living room, darkened backdrop"></div>
<div class="fill news-y1"></div><div class="fill news-y2"></div><div class="fill news-y3"></div>
<h2 class="sec-title news-title">Sign Up For Our Newsletter</h2>
<div class="inp" style="left:162px;width:313px">Enter Name :</div>
<div class="inp" style="left:485px;width:313px">Email Address :</div>
<div class="btn" style="left:808px;top:3753px;width:230px;background:var(--yellow);color:var(--ink)">Subcribe Now</div>

<!-- footer -->
<div class="abs logo f-logo"><span class="logo-dot"></span><span class="logo-name">Copper Fern Services</span></div>
<div class="abs f-contact">
  <div><svg width="20" height="20" viewBox="0 0 24 24"><path d="M6.6 10.8a15 15 0 006.6 6.6l2.2-2.2c.3-.3.7-.4 1-.2 1.1.4 2.3.6 3.6.6.6 0 1 .4 1 1V20c0 .6-.4 1-1 1A17 17 0 013 4c0-.6.4-1 1-1h3.5c.6 0 1 .4 1 1 0 1.3.2 2.5.6 3.6.1.3 0 .7-.2 1z" fill="#e9b308"/></svg>123.456.7890</div>
  <div><svg width="20" height="16" viewBox="0 0 20 16"><rect width="20" height="16" rx="2" fill="#e9b308"/><path d="M1 2l9 7 9-7" stroke="#fff" stroke-width="1.5" fill="none"/></svg>info@copperfernductless.com</div>
  <div><svg width="20" height="24" viewBox="0 0 20 24"><path d="M10 0a8 8 0 018 8c0 6-8 16-8 16S2 14 2 8a8 8 0 018-8z" fill="#e9b308"/><circle cx="10" cy="8" r="3" fill="#fff"/></svg>123,Address, Street Name,<br>City Name, Zipcode</div>
</div>
<div class="f-col" style="left:348px"><h5>NAVIGATION</h5><ul><li>- Home</li><li>- About Us</li><li>- Services</li><li>- Testimonials</li><li>- Finance</li></ul></div>
<div class="f-col" style="left:616px"><h5>Company</h5><ul><li>- Blog</li><li>- Finance</li><li>- Faqs</li><li>- Tems &amp; Conditions</li><li>- Privacy Policy</li></ul></div>
<div class="f-col" style="left:885px"><h5>GET STARTED NOW</h5></div>
<div class="f-inp" style="top:4052px">Name :</div>
<div class="f-inp" style="top:4104px">Email :</div>
<div class="f-inp" style="top:4156px">Phone :</div>
<div class="f-inp" style="top:4208px">Message :</div>
<div class="btn" style="left:932px;top:4264px;width:190px;height:42px;font-size:14px">Submit Now</div>
<div class="abs copy">© COPPER FERN DUCTLESS EXPERTS SERVICES - 2019. All Rights Reserved.</div>

</body>
</html>
```